International Travel Technology R&D business needs a wordpress website

We are a start up team of initially 2 individuals but plan to grow our team quickly, we have deep experience in travel technology. Our goal is to provide next generation technology research and development on behalf of our clients who are leading players in the travel technology industry. Attached our logos.

Target Market(s)

Travel Technology companies

Industry/Entity Type

Travel Industry

Coding

Coded - Design and coding required

Font styles to use
Sans Serif

Requirements
Must have
• Make use of our logo and colour scheme in the attached. Has to have a sense of adventure/ stepping into the unknown but equally must convey a sense of professionalism , we are a safe pair of hands. Sample themes are in the attachment .
Nice to have
• We have identified a theme on skinharbor which we feel would be inspirational. We hahe attached them to help in the design as inspiration.
Should not have
• images of airplanes , hotels etc, we want to project a future image.

```html
<!DOCTYPE html>
<html lang="en">
<head>
<meta charset="utf-8">
<title>Wayfield Labs</title>
<link href="https://fonts.googleapis.com/css2?family=Open+Sans:wght@400;600;700&family=Raleway:wght@400;600;700;800&display=swap" rel="stylesheet">
<style>
:root{
  --green:#6aa236;
  --green-dark:#5b8f2c;
  --navy:#1c2a6b;
  --ink:#222;
  --text:#777;
  --light:#f2f2f2;
  --footer:#2a2a2a;
  --white:#fff;
}
*{box-sizing:border-box;margin:0;padding:0}
html,body{width:1200px;height:3203px;overflow:hidden;background:var(--white)}
body{font-family:"Open Sans",Arial,sans-serif;color:var(--text);position:relative}
section,header,footer{position:absolute;left:0;width:1200px}
.abs{position:absolute}
.h-section{font-family:"Raleway",Arial,sans-serif;font-weight:700;font-size:26px;color:var(--ink);text-align:center;width:100%;letter-spacing:.5px}
.btn-outline{border:2px solid #d6d6d6;color:var(--green);font-family:"Raleway",sans-serif;font-weight:700;font-size:13px;display:flex;align-items:center;justify-content:center;width:124px;height:34px}

/* header */
.site-header{top:0;height:85px;border-top:4px solid var(--navy);background:var(--white);box-shadow:0 1px 0 #e5e5e5}
.brand{left:98px;top:14px;color:var(--navy);font-family:"Raleway",sans-serif;text-align:center;width:220px}
.brand-name{font-size:30px;font-weight:700;letter-spacing:1px;line-height:32px}
.brand-sub{font-size:13px;letter-spacing:12px;color:var(--green);line-height:18px}
.main-nav{right:94px;top:32px;display:flex;gap:26px;font-family:"Raleway",sans-serif;font-size:14px;font-weight:600;color:var(--ink);text-transform:uppercase;align-items:center}
.main-nav .active{color:var(--green)}

/* hero */
.hero{top:85px;height:449px}
.hero-photo{position:absolute;inset:0;background:linear-gradient(100deg,#3e4a2a 0%,#6d6a45 30%,#9a7a4e 55%,#b98f60 70%,#6e6a4c 100%)}
.hero-title{left:98px;top:124px;font-family:"Raleway",sans-serif;font-weight:800;font-size:50px;color:var(--white);letter-spacing:1px}
.hero-text{left:98px;top:197px;width:540px;font-size:15px;line-height:24px;color:var(--white);font-weight:600}
.hero-btn{left:98px;top:271px;width:158px;height:41px;background:var(--green);color:var(--white);font-family:"Raleway",sans-serif;font-weight:700;font-size:14px;display:flex;align-items:center;justify-content:center}
.dots{display:flex;gap:6px}
.dot{width:14px;height:14px;border-radius:50%;border:2px solid var(--white)}
.dot.on{background:var(--green);border-color:var(--white)}
.hero .dots{left:560px;top:395px}

/* welcome */
.welcome{top:534px;height:476px}
.welcome .h-section{top:50px;position:absolute}
.welcome-intro{left:190px;top:96px;width:820px;text-align:center;font-size:12.5px;line-height:21px}
.service{top:172px;width:230px;text-align:center}
.service-icon{width:120px;height:120px;border-radius:50%;border:4px solid var(--navy);margin:0 auto;display:flex;align-items:center;justify-content:center}
.service-icon.green{border-color:var(--green)}
.service h3{font-family:"Raleway",sans-serif;font-size:16px;font-weight:700;color:var(--ink);margin-top:22px}
.service p{font-size:12.5px;line-height:21px;margin-top:10px}
.service .more{margin-top:14px;color:var(--green);font-family:"Raleway",sans-serif;font-weight:700;font-size:13px}

/* who we are */
.about{top:1010px;height:414px;background:var(--light)}
.about-photo{left:0;top:0;width:600px;height:414px;background:linear-gradient(135deg,#5b7ea6 0%,#c9b59b 40%,#e9dfd3 65%,#9fb3c7 100%)}
.about h2{left:651px;top:38px;font-family:"Raleway",sans-serif;font-weight:700;font-size:26px;color:var(--ink)}
.about-intro{left:651px;top:92px;width:460px;font-size:12.5px;line-height:21px}
.checks{left:651px;top:150px;list-style:none;font-size:12.5px}
.checks li{display:flex;align-items:center;gap:14px;height:35px}
.about .btn-outline{left:651px;top:339px;background:transparent}

/* stats */
.stats{top:1424px;height:280px;background:linear-gradient(100deg,#6aa236 0%,#78ad43 45%,#8fbe5a 65%,#6aa236 100%)}
.stat{top:38px;width:240px;text-align:center;color:var(--white)}
.stat-ring{width:128px;height:128px;border-radius:50%;border:3px solid var(--white);margin:0 auto;display:flex;align-items:center;justify-content:center}
.stat-num{font-family:"Raleway",sans-serif;font-weight:700;font-size:32px;line-height:36px;margin-top:12px}
.stat-label{font-size:15px;line-height:18px}

/* blog */
.blog{top:1704px;height:574px}
.blog .h-section{position:absolute;top:50px}
.post{top:113px;width:320px}
.post-photo{width:320px;height:218px}
.post h3{font-family:"Raleway",sans-serif;font-size:15.5px;font-weight:700;color:var(--ink);margin-top:20px}
.post-meta{font-size:12px;color:var(--navy);margin-top:8px;display:flex;align-items:center;gap:6px}
.post p{font-size:12.5px;line-height:21px;margin-top:12px}
.post .btn-outline{margin-top:16px}
.arrow{color:#bbb;font-size:34px;line-height:34px;font-family:"Open Sans",sans-serif}

/* testimonial */
.quote-band{top:2278px;height:391px}
.quote-photo{position:absolute;inset:0;background:linear-gradient(90deg,#2d2e3a 0%,#5a5e6c 30%,#7b7f8c 50%,#55586a 70%,#2b2a36 100%)}
.quote-band .inner{position:absolute;left:0;width:1200px;text-align:center;color:var(--white)}
.quote-title{top:124px;font-family:"Raleway",sans-serif;font-weight:700;font-size:22px}
.quote-text{top:205px;left:180px!important;width:840px!important;font-size:13px;line-height:24px;font-style:italic}
.quote-name{top:280px;font-family:"Raleway",sans-serif;font-weight:700;font-size:14px}
.quote-band .dots{left:578px;top:324px}
.quote-band .dot{width:12px;height:12px;border:none;background:var(--white)}
.quote-band .dot.on{background:var(--green)}

/* partners */
.partners{top:2669px;height:245px}
.partners .h-section{position:absolute;top:50px}
.partner-row{left:183px;top:116px;display:flex;gap:17px}
.partner{width:152px;height:70px;border:2px solid #e2e2e2;display:flex;align-items:center;justify-content:center}
.partner span{display:block;width:96px;height:26px;border-radius:4px}

/* footer */
.site-footer{top:2914px;height:289px;background:var(--footer);border-top:4px solid var(--navy);color:#ddd}
.foot-brand{left:98px;top:72px;width:245px;text-align:center;color:var(--white);font-family:"Raleway",sans-serif}
.foot-brand .brand-name{font-size:34px;letter-spacing:1px}
.foot-brand .brand-sub{color:var(--white);font-size:15px;letter-spacing:14px}
.foot-h{font-family:"Raleway",sans-serif;font-weight:700;font-size:16px;color:var(--white)}
.foot-links{list-style:none;font-size:12px;line-height:16px;margin-top:22px}
.news p{font-size:12px;line-height:18px;margin-top:22px;width:220px}
.news .field{margin-top:12px;width:212px;height:34px;background:var(--white);color:#999;font-size:12px;display:flex;align-items:center;padding-left:12px}
.news .sub{margin-top:14px;width:100px;height:34px;border:2px solid var(--white);color:var(--white);font-family:"Raleway",sans-serif;font-weight:700;font-size:12px;display:flex;align-items:center;justify-content:center}
.contact-list{list-style:none;font-size:12px;margin-top:20px}
.contact-list li{display:flex;gap:20px;line-height:16px;margin-bottom:14px}
.foot-rule{left:98px;top:234px;width:1004px;height:1px;background:#444}
.copyright{left:98px;top:254px;font-size:12px}
.social{right:98px;top:248px;display:flex;gap:6px}
.social span{width:26px;height:26px;border:2px solid #ccc;border-radius:50%}
</style>
</head>
<body>

<header class="site-header">
  <div class="abs brand"><div class="brand-name">WAYFIELD</div><div class="brand-sub">LABS</div></div>
  <nav class="abs main-nav">
    <span class="active">Home</span><span>About Us</span><span>Services</span><span>Features</span><span>Partners</span><span>News</span><span>Blog</span><span>Contact Us</span>
    <svg width="14" height="14" viewBox="0 0 14 14"><circle cx="6" cy="6" r="4.5" fill="none" stroke="#222" stroke-width="2"/><line x1="9.5" y1="9.5" x2="13" y2="13" stroke="#222" stroke-width="2"/></svg>
  </nav>
</header>

<section class="hero">
  <div class="hero-photo" role="img" aria-label="Traveller seated on a rocky cliff edge overlooking a wide forested valley"></div>
  <h1 class="abs hero-title">WAYFIELD LABS</h1>
  <p class="abs hero-text">Our goal is to provide next generation technology research and development on behalf of our clients who are leading players in the travel technology industry.</p>
  <div class="abs hero-btn">GET MORE INFO &gt;&gt;</div>
  <div class="abs dots"><span class="dot on"></span><span class="dot"></span><span class="dot"></span><span class="dot"></span></div>
</section>

<section class="welcome">
  <h2 class="h-section">WELCOME TO WAYFIELD LABS</h2>
  <p class="abs welcome-intro">At vero eos et accusamus et iusto odio dignissimos ducimus qui blanditiis praesentium voluptatum deleniti atque corrupti quos dolores et quas molestias excepturi sint occaecati cupiditate non provident, similique sunt in culpa qui officia deserunt mollitia animi, id est</p>

  <div class="abs service" style="left:92px">
    <div class="service-icon green"><svg width="52" height="52" viewBox="0 0 24 24"><path fill="#6aa236" d="M21 16v-2l-8-5V3.5a1.5 1.5 0 0 0-3 0V9l-8 5v2l8-2.5V19l-2 1.5V22l3.5-1 3.5 1v-1.5L13 19v-5.5z"/></svg></div>
    <h3>TRAVEL AGENCIES</h3>
    <p>Nam libero tempore, cum soluta nob est eligendi optio cumque nihil impedit quo minus id quod max</p>
    <div class="more">READ MORE &gt;&gt;</div>
  </div>
  <div class="abs service" style="left:353px">
    <div class="service-icon"><svg width="52" height="52" viewBox="0 0 24 24" fill="none" stroke="#1c2a6b" stroke-width="2"><rect x="3" y="5" width="14" height="15" rx="2"/><path d="M10 14l9-9 2 2-9 9h-2z"/></svg></div>
    <h3>BOOKING ENGINE</h3>
    <p>Nam libero tempore, cum soluta nob est eligendi optio cumque nihil impedit quo minus id quod max</p>
    <div class="more">READ MORE &gt;&gt;</div>
  </div>
  <div class="abs service" style="left:615px">
    <div class="service-icon"><svg width="58" height="58" viewBox="0 0 24 24" fill="#1c2a6b"><circle cx="9" cy="13" r="5"/><circle cx="9" cy="13" r="2" fill="#fff"/><circle cx="17" cy="7" r="3.5"/><circle cx="17" cy="7" r="1.3" fill="#fff"/><circle cx="18" cy="17" r="2.5"/></svg></div>
    <h3>SEARCH OPTIMIZATION</h3>
    <p>Nam libero tempore, cum soluta nob est eligendi optio cumque nihil impedit quo minus id quod max</p>
    <div class="more">READ MORE &gt;&gt;</div>
  </div>
  <div class="abs service" style="left:876px">
    <div class="service-icon"><svg width="52" height="52" viewBox="0 0 24 24" fill="#1c2a6b"><circle cx="12" cy="8" r="5"/><path d="M3 22c0-5 4-8 9-8s9 3 9 8z"/></svg></div>
    <h3>CONSOLIDATORS</h3>
    <p>Nam libero tempore, cum soluta nob est eligendi optio cumque nihil impedit quo minus id quod max</p>
    <div class="more">READ MORE &gt;&gt;</div>
  </div>
</section>

<section class="about">
  <div class="abs about-photo" role="img" aria-label="Consultant meeting with a smiling couple at a desk in front of a world map"></div>
  <h2 class="abs">WHO WE ARE</h2>
  <p class="abs about-intro">Nam libero tempore, cum soluta nobis est eligendi optio cumque nihil impedquo minus id quod maxime placeat facere possimus.</p>
  <ul class="abs checks">
    <li><svg width="14" height="14" viewBox="0 0 14 14"><circle cx="7" cy="7" r="7" fill="#6aa236"/><path d="M4 7l2 2 4-4" stroke="#fff" stroke-width="1.8" fill="none"/></svg>Nam libero tempore, cum soluta nobis est eligendi optio</li>
    <li><svg width="14" height="14" viewBox="0 0 14 14"><circle cx="7" cy="7" r="7" fill="#6aa236"/><path d="M4 7l2 2 4-4" stroke="#fff" stroke-width="1.8" fill="none"/></svg>Omnis voluptas assumenda est, omnis dolor repellendus</li>
    <li><svg width="14" height="14" viewBox="0 0 14 14"><circle cx="7" cy="7" r="7" fill="#6aa236"/><path d="M4 7l2 2 4-4" stroke="#fff" stroke-width="1.8" fill="none"/></svg>Temporibus autem quibusdam et aut officiis debitis aut rerum</li>
    <li><svg width="14" height="14" viewBox="0 0 14 14"><circle cx="7" cy="7" r="7" fill="#6aa236"/><path d="M4 7l2 2 4-4" stroke="#fff" stroke-width="1.8" fill="none"/></svg>Ut aut reiciendis voluptatibus maiores alias conseq</li>
    <li><svg width="14" height="14" viewBox="0 0 14 14"><circle cx="7" cy="7" r="7" fill="#6aa236"/><path d="M4 7l2 2 4-4" stroke="#fff" stroke-width="1.8" fill="none"/></svg>Ut enim ad minima veniam, quis nostrum exercitationem</li>
  </ul>
  <div class="abs btn-outline">READ MORE &gt;&gt;</div>
</section>

<section class="stats">
  <div class="abs stat" style="left:59px">
    <div class="stat-ring"><svg width="56" height="56" viewBox="0 0 24 24" fill="none" stroke="#fff" stroke-width="2.4"><path d="M4 8h15M15 4l4 4-4 4M20 16H5M9 12l-4 4 4 4"/></svg></div>
    <div class="stat-num">25</div><div class="stat-label">Integrations</div>
  </div>
  <div class="abs stat" style="left:341px">
    <div class="stat-ring"><svg width="56" height="56" viewBox="0 0 24 24" fill="none" stroke="#fff" stroke-width="2"><rect x="3" y="5" width="14" height="15" rx="2"/><path d="M10 14l9-9 2 2-9 9h-2z"/></svg></div>
    <div class="stat-num">50k+</div><div class="stat-label">Bookings a day</div>
  </div>
  <div class="abs stat" style="left:623px">
    <div class="stat-ring"><svg width="60" height="60" viewBox="0 0 24 24" fill="#fff"><path d="M6 19a4 4 0 0 1-.5-8A6 6 0 0 1 17 9a5 5 0 0 1 1 10z"/></svg></div>
    <div class="stat-num">30k+</div><div class="stat-label">Cloud Hosting</div>
  </div>
  <div class="abs stat" style="left:905px">
    <div class="stat-ring"><svg width="62" height="62" viewBox="0 0 24 24" fill="#fff"><circle cx="12" cy="8" r="3.2"/><path d="M6 19c0-4 3-6 6-6s6 2 6 6z"/><circle cx="5.5" cy="10" r="2.3"/><path d="M1 18c0-3 2-5 4.5-5 1 0 1.7.3 2 .6C6 15 5.5 16.5 5.5 18z"/><circle cx="18.5" cy="10" r="2.3"/><path d="M23 18c0-3-2-5-4.5-5-1 0-1.7.3-2 .6 1.5 1.4 2 2.9 2 4.4z"/></svg></div>
    <div class="stat-num">40k+</div><div class="stat-label">Customer Served</div>
  </div>
</section>

<section class="blog">
  <h2 class="h-section">LATEST BLOG</h2>
  <div class="abs arrow" style="left:66px;top:203px">&#8249;</div>
  <div class="abs arrow" style="left:1118px;top:203px">&#8250;</div>

  <article class="abs post" style="left:98px">
    <div class="post-photo" role="img" aria-label="Team of colleagues reviewing documents and a tablet together" style="background:linear-gradient(135deg,#3a4f6e,#8fa2b8 55%,#d8dde3)"></div>
    <h3>At vero eos et accusamus et iusto odignissi</h3>
    <div class="post-meta"><svg width="11" height="11" viewBox="0 0 12 12"><rect x="1" y="2" width="10" height="9" fill="#1c2a6b"/></svg>23/08/2016 &nbsp;| <svg width="10" height="11" viewBox="0 0 10 11"><circle cx="5" cy="3" r="2.5" fill="#1c2a6b"/><path d="M0 11c0-3 2-5 5-5s5 2 5 5z" fill="#1c2a6b"/></svg>John</div>
    <p>Nam libero tempore, cum soluta nobis est eligendi optio cumque nihil impedit quo minus id quod maximeplaceat facere possimus mnis voluptas assumen.</p>
    <div class="btn-outline">READ MORE &gt;&gt;</div>
  </article>
  <article class="abs post" style="left:440px">
    <div class="post-photo" role="img" aria-label="Businessman in a suit presenting at an office window" style="background:linear-gradient(135deg,#b9c7d6,#6e7d8f 50%,#e4e8ec)"></div>
    <h3>At vero eos et accusamus et iusto odignissi</h3>
    <div class="post-meta"><svg width="11" height="11" viewBox="0 0 12 12"><rect x="1" y="2" width="10" height="9" fill="#1c2a6b"/></svg>23/08/2016 &nbsp;| <svg width="10" height="11" viewBox="0 0 10 11"><circle cx="5" cy="3" r="2.5" fill="#1c2a6b"/><path d="M0 11c0-3 2-5 5-5s5 2 5 5z" fill="#1c2a6b"/></svg>John</div>
    <p>Nam libero tempore, cum soluta nobis est eligendi optio cumque nihil impedit quo minus id quod maximeplaceat facere possimus mnis voluptas assumen.</p>
    <div class="btn-outline">READ MORE &gt;&gt;</div>
  </article>
  <article class="abs post" style="left:781px">
    <div class="post-photo" role="img" aria-label="Two colleagues working together at a laptop in a bright office" style="background:linear-gradient(135deg,#d9e2ea,#8fa3b6 45%,#4f6378)"></div>
    <h3>At vero eos et accusamus et iusto odignissi</h3>
    <div class="post-meta"><svg width="11" height="11" viewBox="0 0 12 12"><rect x="1" y="2" width="10" height="9" fill="#1c2a6b"/></svg>23/08/2016 &nbsp;| <svg width="10" height="11" viewBox="0 0 10 11"><circle cx="5" cy="3" r="2.5" fill="#1c2a6b"/><path d="M0 11c0-3 2-5 5-5s5 2 5 5z" fill="#1c2a6b"/></svg>John</div>
    <p>Nam libero tempore, cum soluta nobis est eligendi optio cumque nihil impedit quo minus id quod maximeplaceat facere possimus mnis voluptas assumen.</p>
    <div class="btn-outline">READ MORE &gt;&gt;</div>
  </article>
</section>

<section class="quote-band">
  <div class="quote-photo" role="img" aria-label="Blurred silhouettes of business people walking past tall windows"></div>
  <div class="inner" style="top:50px"><svg width="62" height="50" viewBox="0 0 62 50" fill="#fff"><path d="M0 22C0 8 8 1 22 0v9c-7 1-11 5-11 11h11v30H0zM34 22C34 8 42 1 56 0v9c-7 1-11 5-11 11h11v30H34z" transform="scale(1.05 1)"/></svg></div>
  <div class="inner quote-title">Nemo enim ipsam voluptatem quia voluptas</div>
  <div class="inner quote-text">“ At vero eos et accusamus et iusto odio dignissimos ducimus qui blanditiis praesentium voluptatum deleniti atque corrupti quos dolores et quas molestias excepturi sint occaecati cupidimilique sunt in culpa qui officia deserunt mollitia animi. ”</div>
  <div class="inner quote-name">JOHN DOE</div>
  <div class="abs dots"><span class="dot on"></span><span class="dot"></span><span class="dot"></span></div>
</section>

<section class="partners">
  <h2 class="h-section">OUR PARTNERS</h2>
  <div class="abs arrow" style="left:96px;top:130px">&#8249;</div>
  <div class="abs arrow" style="left:1086px;top:130px">&#8250;</div>
  <div class="abs partner-row">
    <div class="partner"><span style="background:#1c5ea8"></span></div>
    <div class="partner"><span style="background:#9fb4c8"></span></div>
    <div class="partner"><span style="background:#3a3a3a"></span></div>
    <div class="partner"><span style="background:#6a8fbf"></span></div>
    <div class="partner"><span style="background:#8bb55a"></span></div>
  </div>
</section>

<footer class="site-footer">
  <div class="abs foot-brand"><div class="brand-name">WAYFIELD</div><div class="brand-sub">LABS</div></div>
  <div class="abs" style="left:421px;top:40px">
    <div class="foot-h">Information</div>
    <ul class="foot-links"><li>Home</li><li>About Us</li><li>Services</li><li>Features</li><li>Partners</li><li>News</li><li>Blog</li><li>Contact Us</li></ul>
  </div>
  <div class="abs news" style="left:589px;top:40px">
    <div class="foot-h">Newsletter Subscription</div>
    <p>Register your email address to get information about us</p>
    <div class="field">Email Address</div>
    <div class="sub">SUBSCRIBE</div>
  </div>
  <div class="abs" style="left:925px;top:40px">
    <div class="foot-h">Contact Us</div>
    <ul class="contact-list">
      <li><svg width="10" height="14" viewBox="0 0 10 14"><path d="M5 0a5 5 0 0 1 5 5c0 4-5 9-5 9S0 9 0 5a5 5 0 0 1 5-5z" fill="#fff"/><circle cx="5" cy="5" r="1.8" fill="#2a2a2a"/></svg><span>418 North Harrow Lane<br>Denver, CO 80204</span></li>
      <li><svg width="12" height="12" viewBox="0 0 24 24"><path fill="#fff" d="M6.6 10.8a15 15 0 0 0 6.6 6.6l2.2-2.2a1 1 0 0 1 1-.25 11 11 0 0 0 3.6.6 1 1 0 0 1 1 1V20a1 1 0 0 1-1 1A17 17 0 0 1 3 4a1 1 0 0 1 1-1h3.5a1 1 0 0 1 1 1c0 1.25.2 2.45.6 3.6a1 1 0 0 1-.25 1z"/></svg><span>1 555 010 2040</span></li>
      <li><svg width="12" height="12" viewBox="0 0 12 12"><rect x="0" y="3" width="12" height="9" fill="#fff"/><rect x="3" y="0" width="6" height="4" fill="#fff"/></svg><span>1 555 010 2041</span></li>
      <li><svg width="12" height="10" viewBox="0 0 12 10"><rect width="12" height="10" fill="#fff"/><path d="M0 0l6 5 6-5" stroke="#2a2a2a" fill="none"/></svg><span>info@wayfieldlabs.com</span></li>
    </ul>
  </div>
  <div class="abs foot-rule"></div>
  <div class="abs copyright">Copyrights © 2016, Wayfield Labs. All rights reserved.</div>
  <div class="abs social"><span></span><span></span><span></span><span></span></div>
</footer>

</body>
</html>
```